TA BRAMLEY BUSINESS CARD DESIGN PROJECT

We need to utilize our logo that was expertly created on PixelHarbor and now need to match this with a business card design.

```html
<!DOCTYPE html>
<html lang="en">
<head>
<meta charset="utf-8">
<title>TA BRAMLEY Business Card</title>
<link href="https://fonts.googleapis.com/css2?family=Montserrat:wght@400;500;700&display=swap" rel="stylesheet">
<style>
  :root {
    --brand-blue: #0f57ac;
    --card-black: #1b1b1b;
    --ink-white: #ffffff;
    --stage: #e9e9ea;
  }
  * { margin: 0; padding: 0; box-sizing: border-box; }
  html, body { width: 1200px; height: 900px; overflow: hidden; }
  body {
    background: var(--stage);
    font-family: "Montserrat", sans-serif;
    position: relative;
  }
  .card {
    position: absolute;
    left: 270px;
    width: 660px;
    height: 377px;
    border-radius: 22px;
    overflow: hidden;
    box-shadow: 0 6px 18px rgba(0,0,0,0.18);
  }
  .card--front { top: 56px; background: var(--brand-blue); }
  .card--back { top: 467px; background: var(--card-black); }

  .brand-name {
    position: absolute;
    font-weight: 700;
    letter-spacing: 0.12em;
    white-space: nowrap;
  }
  .card--front .brand-name {
    color: var(--ink-white);
    font-size: 58px;
    left: 0; right: 0; top: 150px;
    text-align: center;
  }
  .card--back .brand-name {
    color: var(--brand-blue);
    font-size: 30px;
    left: 44px; top: 170px;
  }

  .divider {
    position: absolute;
    left: 318px; top: 70px;
    width: 2px; height: 237px;
    background: var(--brand-blue);
  }
  .contact {
    position: absolute;
    left: 348px; top: 72px;
    color: var(--ink-white);
  }
  .contact__name {
    color: var(--brand-blue);
    font-weight: 700;
    font-size: 21px;
    letter-spacing: 0.02em;
  }
  .contact__role { font-size: 14px; margin-top: 2px; }
  .contact__list { list-style: none; margin-top: 18px; }
  .contact__item {
    display: flex; align-items: center; gap: 9px;
    font-size: 14px; line-height: 24px;
  }
  .contact__item svg { width: 13px; height: 13px; fill: var(--brand-blue); flex: none; }
  .contact__address { font-size: 14px; line-height: 21px; margin-top: 14px; padding-left: 22px; }
</style>
</head>
<body>
  <section class="card card--front">
    <div class="brand-name">TA BRAMLEY</div>
  </section>

  <section class="card card--back">
    <div class="brand-name">TA BRAMLEY</div>
    <div class="divider"></div>
    <div class="contact">
      <div class="contact__name">MARCUS HALE</div>
      <div class="contact__role">Managing Director</div>
      <ul class="contact__list">
        <li class="contact__item">
          <svg viewBox="0 0 16 16" aria-hidden="true"><path d="M3 1l3 3-2 2c1 2 3 4 6 6l2-2 3 3-2 2C7 15 1 9 1 3z"/></svg>
          123 456 789
        </li>
        <li class="contact__item">
          <svg viewBox="0 0 16 16" aria-hidden="true"><path d="M4 1h7v4H4zM2 6h12v9H2zm3 2v2h2V8zm4 0v2h2V8zm-4 3v2h2v-2zm4 0v2h2v-2z"/></svg>
          123 456 789
        </li>
        <li class="contact__item">
          <svg viewBox="0 0 16 16" aria-hidden="true"><path d="M1 3h14v1L8 9 1 4zm0 3l7 5 7-5v7H1z"/></svg>
          info@yourgmail.com
        </li>
        <li class="contact__item">
          <svg viewBox="0 0 16 16" aria-hidden="true"><circle cx="8" cy="8" r="7"/></svg>
          www.yourwebsite.com
        </li>
      </ul>
      <div class="contact__address">Your address, City<br>State, Zip 1234</div>
    </div>
  </section>
</body>
</html>
```